Private label Bottled water label design

We are launching private label water bottle case packs with our brand “tallyway”
Need bottle labels design as well as case pack design artwork. Bottle is 16.9oz similar to pet brovani quellin bottles.
It will be spring water.
Case pack will be of 24 bottles
Tallyway is a chain of convenience stores in Texas
www.tallywaymarkets.example
I have attached pictures of brovani water. It would be similar packaging for single and case pack.

Target Market(s)

Male female shoppers middle aged. Take home package or single serve in cold vault

Industry/Entity Type

Water bottle retail

Colors
0054AA
0677BA
7BADD7
CADEEF
E8F1F8
59FF00
82FF00
B8FF75
E3FFCB
F4FFEA

Requirements
Must have
• Very premium look. Use the logo of tallyway
Nice to have
• Elegant premium water look
Should not have
• I am open to all

```html
<!DOCTYPE html>
<html lang="en">
<head>
<meta charset="utf-8">
<title>Tallyway Mountain Spring Water – Bottle Label</title>
<link rel="stylesheet" href="https://fonts.googleapis.com/css2?family=Open+Sans:wght@800&family=Lexend:wght@300;400&display=swap">
<style>
  :root {
    --backdrop: #d3e2c8;
    --label-black: #1c1c1c;
    --lime: #a6d32a;
    --lime-pattern: rgba(166, 211, 42, 0.30);
    --lime-fade: rgba(166, 211, 42, 0.06);
    --snow: #e6ecd8;
    --white: #ffffff;
  }
  html, body {
    margin: 0;
    padding: 0;
    width: 934px;
    height: 1200px;
    overflow: hidden;
    background: var(--backdrop);
  }
  .canvas {
    position: relative;
    width: 934px;
    height: 1200px;
  }
  .label {
    position: absolute;
    left: 87px;
    top: 297px;
    width: 760px;
    height: 606px;
    background: var(--label-black);
    overflow: hidden;
  }
  .label__pattern {
    position: absolute;
    left: 0;
    top: 0;
    width: 100%;
    height: 400px;
    background: linear-gradient(180deg, var(--lime-pattern) 0%, var(--lime-fade) 75%, transparent 100%);
  }
  .label__brand {
    position: absolute;
    left: 0;
    top: 150px;
    width: 100%;
    text-align: center;
    font-family: "Open Sans", sans-serif;
    font-weight: 800;
    font-size: 128px;
    line-height: 1;
    letter-spacing: -6px;
    color: var(--white);
  }
  .label__mountains {
    position: absolute;
    left: 229px;
    top: 370px;
    width: 297px;
    height: 94px;
    border-radius: 6px;
    background: linear-gradient(180deg, var(--snow) 0%, var(--lime) 100%);
  }
  .label__volume {
    position: absolute;
    left: 122px;
    top: 510px;
    font-family: "Lexend", sans-serif;
    font-weight: 300;
    font-size: 20px;
    color: var(--lime);
  }
  .label__product {
    position: absolute;
    left: 0;
    top: 482px;
    width: 100%;
    text-align: center;
    font-family: "Lexend", sans-serif;
    font-weight: 400;
    font-size: 29px;
    line-height: 1.1;
    letter-spacing: 1px;
    color: var(--white);
  }
  .label__badge {
    position: absolute;
    left: 590px;
    top: 494px;
  }
</style>
</head>
<body>
  <main class="canvas">
    <section class="label">
      <div class="label__pattern" role="img" aria-label="Fine lime chevron line pattern across the upper label"></div>
      <div class="label__brand">tallyway</div>
      <div class="label__mountains" role="img" aria-label="Snow-capped mountain range illustration in white and lime"></div>
      <div class="label__volume">16,9 oz</div>
      <div class="label__product">Mountain Spring<br>Water</div>
      <svg class="label__badge" width="48" height="48" viewBox="0 0 48 48" aria-hidden="true">
        <circle cx="24" cy="24" r="22" fill="none" stroke="var(--lime)" stroke-width="2.5"/>
      </svg>
    </section>
  </main>
</body>
</html>
```